QRV Advisors needs a web site

We need a web site for www.qrvadvisors-example.com. QRV is a mergers and acquisition consulting company that focuses our buyer and seller services on logistics companies. We help put companies together, and help with legal and financial due diligence. We want the web site to express our service and show the logistics components. We want personalized images versus pictures of trucks and airplanes.

Our new logo uses Burgandy and grey colors. Image attached. We are not in to bold, big letters...classy, artistic, low key preferred. Confidentiality, experience, professional are what we want to express on the site.

All we expect for the first part of this project is a home page, and one subpage.  We are budgeting other funds for the technical aspects of the web site

Reason: All that I'm seeing so far is trucks, forklifts and planes. We are a legal mergers and acquisitions firm that focus on logistics. I like some of the images to say logistics, but really want it say legal, financial, and putting companies together. Will pay extra for the sub page if someone can impress us with a home page.

Reason: Swamped with another project at the moment...will work on this over the weekend and provide designer feedback and select final design by Tuesday

```html
<!DOCTYPE html>
<html lang="en">
<head>
<meta charset="utf-8">
<title>QRV Advisors — Home</title>
<link href="https://fonts.googleapis.com/css2?family=Play:wght@400;700&family=Ubuntu:wght@400;500;700&family=Arimo:wght@400;700&display=swap" rel="stylesheet">
<style>
:root{
  --burgundy:#a50a35;
  --burgundy-dark:#7e0727;
  --grey-dark:#5a5a5c;
  --grey-mid:#8a8a8a;
  --text:#333;
  --text-soft:#555;
  --page:#f2f2f2;
  --footer:#2e2e2e;
  --line:#c9c9c9;
  --white:#fff;
}
*{box-sizing:border-box;margin:0;padding:0}
html,body{width:1028px;height:1200px;overflow:hidden;background:var(--page)}
body{font-family:"Arimo",sans-serif;color:var(--text)}
.page{position:relative;width:1028px;height:1200px;overflow:hidden;background:var(--page)}
.abs{position:absolute}

/* header */
.topbar{left:0;top:0;width:1028px;height:6px;background:#555}
.header{left:0;top:6px;width:1028px;height:118px;background:linear-gradient(#fdfdfd,#e4e4e4)}
.brand{left:120px;top:50px;display:flex;align-items:center;gap:10px}
.brand-mark{width:14px;height:14px;background:var(--burgundy)}
.brand-name{font-family:"Ubuntu",sans-serif;font-size:26px;font-weight:500;color:var(--grey-dark);letter-spacing:1px}
.social{top:23px;display:flex;gap:14px;left:648px}
.social span{width:28px;height:28px;border-radius:50%;background:linear-gradient(#777,#333)}
.call{left:776px;top:22px;display:flex;align-items:center;gap:6px;font-family:"Ubuntu",sans-serif}
.call small{display:block;font-size:11px;color:#444}
.call strong{display:block;font-size:16px;font-weight:400;color:#333}
.nav{left:380px;top:75px;display:flex;gap:15px}
.nav a{display:flex;align-items:center;justify-content:center;text-align:center;height:28px;border-top:1px solid var(--line);border-bottom:1px solid var(--line);font-size:10px;line-height:10px;color:#333;text-decoration:none;text-transform:uppercase;position:relative}
.nav a.current{font-weight:700}
.nav a.current::before{content:"";position:absolute;top:-1px;left:50%;margin-left:-4px;border:4px solid transparent;border-top-color:#333}

/* hero */
.hero{left:0;top:124px;width:1028px;height:376px;background:radial-gradient(circle at 570px 170px,#f5e23a 0,#c9a715 45px,#3a3320 120px,#111 260px),#0d0d0d}
.hero-arrow{top:185px}
.hero-caption{left:118px;top:463px;width:792px;height:37px;background:rgba(240,240,240,.92);font-family:"Arimo",sans-serif;font-weight:700;font-size:19.5px;color:#555;line-height:37px;padding-left:10px}

/* services */
.section-title{left:0;top:515px;width:1028px;text-align:center;font-family:"Play",sans-serif;font-size:25px;color:var(--burgundy)}
.title-rule{top:530px;height:1px;width:225px;background:linear-gradient(90deg,transparent,#aaa,transparent)}
.service{top:563px;width:238px;height:147px;background:var(--white);box-shadow:0 1px 3px rgba(0,0,0,.2)}
.service-head{height:91px;background:var(--grey-dark);position:relative}
.service-head.featured{background:var(--burgundy)}
.service-head h3{position:absolute;left:11px;bottom:5px;font-family:"Play",sans-serif;font-weight:400;font-size:20px;line-height:23px;color:var(--white)}
.service-head svg{position:absolute;right:8px;bottom:0}
.service p{padding:4px 10px;font-family:"Ubuntu",sans-serif;font-size:10px;line-height:15px;color:var(--text-soft)}
.divider{left:0;top:722px;width:1028px;height:14px;background:radial-gradient(ellipse at center,rgba(0,0,0,.1),transparent 70%)}

/* widgets */
.widget{top:772px;width:252px;height:218px}
.widget-body{position:absolute;left:5px;right:5px;top:0;bottom:0;background:linear-gradient(#fff 75%,#ececec);border-radius:4px;box-shadow:0 2px 4px rgba(0,0,0,.15)}
.widget-head{position:absolute;left:0;right:0;top:0;height:31px;background:var(--grey-dark);display:flex;align-items:center;gap:9px;padding-left:12px;font-family:"Ubuntu",sans-serif;font-size:16px;letter-spacing:.5px;color:var(--white);box-shadow:0 2px 2px rgba(0,0,0,.25)}
.about-photo{position:absolute;left:13px;top:48px;width:227px;height:87px;background:linear-gradient(90deg,#cdd4dc,#8d9aa8 40%,#e7ebef 60%,#55606d)}
.about-text{position:absolute;left:19px;top:140px;width:222px;font-size:9.6px;line-height:12px;color:#333}
.more{position:absolute;right:12px;bottom:13px;font-size:9.5px;font-weight:700;color:#444}
.news{position:absolute;left:13px;top:48px;right:10px}
.news-item{display:flex;gap:9px;height:48px}
.date{width:31px;flex:none;text-align:center;box-shadow:0 1px 2px rgba(0,0,0,.25);height:32px}
.date b{display:block;background:var(--burgundy);color:#fff;font-size:11px;line-height:16px}
.date i{display:block;font-style:normal;font-size:9.5px;font-weight:700;line-height:16px;background:#fff}
.news-item p{font-size:9.3px;line-height:12px;color:#333}
.news-item strong{color:#111}
.field{position:absolute;left:17px;width:225px;height:20px;border:1px solid #ccc;border-radius:2px;background:#fff;font-size:10px;color:#555;padding:3px 8px}
.submit{position:absolute;left:18px;top:190px;width:55px;height:19px;background:var(--burgundy);color:#fff;font-family:"Ubuntu",sans-serif;font-weight:700;font-size:12px;text-align:center;line-height:19px}

/* footer */
.footer{left:0;top:1018px;width:1028px;height:182px;background:var(--footer);border-top:3px solid var(--burgundy);color:#eee}
.footer h4{position:absolute;font-family:"Ubuntu",sans-serif;font-weight:400;font-size:15px;color:#eee;padding-bottom:6px;border-bottom:1px dashed #555}
.quick{position:absolute;left:118px;top:51px;list-style:none;font-size:10px;line-height:14.2px}
.quick li::before{content:"›";margin-right:8px;color:#aaa}
.vrule{position:absolute;top:19px;width:1px;height:112px;background:#4a4a4a}
.map{position:absolute;left:288px;top:47px;width:184px;height:81px;background:linear-gradient(135deg,#e9e6df,#d8d4cc);border:2px solid #eee}
.contact-line{position:absolute;left:480px;display:flex;align-items:center;gap:8px;font-size:10.2px;line-height:15px;color:#eee}
.foot-brand{position:absolute;left:730px;top:14px;width:178px;text-align:center;font-family:"Ubuntu",sans-serif;font-weight:500;font-size:52px;letter-spacing:6px;color:#fff}
.foot-social{position:absolute;left:764px;top:96px;display:flex;gap:10px}
.foot-social span{width:31px;height:31px;border-radius:50%;background:#555}
.copyright{position:absolute;left:0;width:1028px;top:147px;text-align:center;font-family:"Ubuntu",sans-serif;font-size:12px;color:#eee}
</style>
</head>
<body>
<div class="page">

  <div class="abs topbar"></div>
  <header class="abs header">
    <div class="abs brand" style="top:44px"><span class="brand-mark"></span><span class="brand-name">QRV Advisors</span></div>
    <div class="abs social"><span></span><span></span><span></span></div>
    <div class="abs call">
      <svg width="28" height="28" viewBox="0 0 28 28"><circle cx="14" cy="14" r="12.5" fill="none" stroke="#a50a35" stroke-width="2"/><path d="M10 8c-1 2 0 6 3 9s6 4 7 2l-2-2-2 1c-2-1-4-3-5-5l1-2z" fill="#a50a35"/></svg>
      <div><small>Call Us Today</small><strong>123 456 7890</strong></div>
    </div>
  </header>
  <nav class="abs nav">
    <a class="current" style="width:40px">Home</a>
    <a style="width:64px">About<br>Us</a>
    <a style="width:80px">Buyer<br>Services</a>
    <a style="width:80px">Seller<br>Services</a>
    <a style="width:80px">News &amp;<br>Events</a>
    <a style="width:40px">FAQ's</a>
    <a style="width:65px">Contact</a>
  </nav>

  <div class="abs hero" role="img" aria-label="Hand beneath a row of sketched light bulbs, the centre bulb glowing yellow against a dark suit"></div>
  <svg class="abs hero-arrow" style="left:80px;top:308px" width="24" height="34"><path d="M20 2 6 17l14 15" fill="none" stroke="#aaa" stroke-width="4"/></svg>
  <svg class="abs hero-arrow" style="left:924px;top:308px" width="24" height="34"><path d="M4 2l14 15L4 32" fill="none" stroke="#aaa" stroke-width="4"/></svg>
  <div class="abs hero-caption">QRV Services Are Offered By Industry Executives With Extensive M&amp;A Experience</div>

  <div class="abs title-rule" style="left:198px"></div>
  <div class="abs title-rule" style="left:616px"></div>
  <h2 class="abs section-title" style="font-weight:400">Our Services</h2>

  <section class="abs service" style="left:119px">
    <div class="service-head featured">
      <h3>Business<br>Planning</h3>
      <svg width="62" height="62" viewBox="0 0 62 62"><path d="M6 6h40v50H6z" fill="none" stroke="#fff" stroke-width="3"/><path d="M13 16h26M13 25h26M13 34h20" stroke="#fff" stroke-width="3"/><path d="M28 46l8 8 20-20" fill="none" stroke="#fff" stroke-width="4"/></svg>
    </div>
    <p>Lorem ipsum dolor sit amet, consectetuer eadi pis elit, sed diam nonummy nibh euismod tinc idunt ut laoreeio dolore magna aliquam erate</p>
  </section>
  <section class="abs service" style="left:394px">
    <div class="service-head">
      <h3>Mergers &amp;<br>Acquisition</h3>
      <svg width="68" height="50" viewBox="0 0 68 50"><path d="M4 14l16-6 14 6 14-6 16 6-6 16-18 14-6-4-6 4-20-14z" fill="#fff"/></svg>
    </div>
    <p>Lorem ipsum dolor sit amet, consectetuer eadi pis elit, sed diam nonummy nibh euismod tinc idunt ut laoreeio dolore magna aliquam erate</p>
  </section>
  <section class="abs service" style="left:670px">
    <div class="service-head">
      <h3>Advisory<br>Services</h3>
      <svg width="60" height="56" viewBox="0 0 60 56"><rect x="26" y="2" width="30" height="22" rx="3" fill="none" stroke="#fff" stroke-width="2.5"/><path d="M31 9h20M31 15h16" stroke="#fff" stroke-width="2"/><circle cx="20" cy="30" r="8" fill="#fff"/><path d="M4 56c0-12 7-17 16-17s16 5 16 17z" fill="#fff"/></svg>
    </div>
    <p>Lorem ipsum dolor sit amet, consectetuer eadi pis elit, sed diam nonummy nibh euismod tinc idunt ut laoreeio dolore magna aliquam erate</p>
  </section>

  <div class="abs divider"></div>

  <section class="abs widget" style="left:118px">
    <div class="widget-body">
      <div class="about-photo" role="img" aria-label="Three colleagues in business attire talking in an office" style="left:8px"></div>
      <p class="about-text" style="left:14px">QRV assists business owners within the logistics industry to implement growth and exit strategies. We offer business planning and merger and acquisition (M&amp;A) advisory services.</p>
      <span class="more">Read More »</span>
    </div>
    <div class="widget-head">
      <svg width="20" height="16" viewBox="0 0 20 16"><circle cx="10" cy="5" r="3.5" fill="#fff"/><circle cx="4" cy="7" r="2.5" fill="#fff"/><circle cx="16" cy="7" r="2.5" fill="#fff"/><path d="M4 16c0-5 3-7 6-7s6 2 6 7zM0 15c0-4 2-5 4-5M20 15c0-4-2-5-4-5" fill="#fff"/></svg>
      ABOUT QRV
    </div>
  </section>

  <section class="abs widget" style="left:390px">
    <div class="widget-body">
      <div class="news" style="left:8px">
        <div class="news-item"><div class="date"><b>Apr</b><i>02</i></div><p><strong>Lorem ipsum dolor sit amet, consectetue</strong> eadi pis elit, sed diam nonummy nibherini euismod tinc idunt ut laoreeio.</p></div>
        <div class="news-item"><div class="date"><b>Apr</b><i>03</i></div><p><strong>Lorem ipsum dolor sit amet, consectetue</strong> eadi pis elit, sed diam nonummy nibherini euismod tinc idunt ut laoreeio.</p></div>
        <div class="news-item"><div class="date"><b>Apr</b><i>04</i></div><p><strong>Lorem ipsum dolor sit amet, consectetue</strong> eadi pis elit, sed diam nonummy nibherini euismod tinc idunt ut laoreeio.</p></div>
      </div>
      <span class="more">Read More »</span>
    </div>
    <div class="widget-head">
      <svg width="16" height="16" viewBox="0 0 16 16"><rect x="1" y="2" width="14" height="13" fill="none" stroke="#fff" stroke-width="1.5"/><path d="M1 5h14" stroke="#fff" stroke-width="2"/><path d="M4 8h2M7 8h2M10 8h2M4 11h2M7 11h2M10 11h2" stroke="#fff" stroke-width="1.5"/></svg>
      NEWS &amp; EVENTS
    </div>
  </section>

  <section class="abs widget" style="left:659px">
    <div class="widget-body">
      <div class="field" style="top:47px">Name</div>
      <div class="field" style="top:75px">Email</div>
      <div class="field" style="top:104px">Phone</div>
      <div class="field" style="top:132px;height:52px">Message</div>
      <div class="submit">Submit</div>
    </div>
    <div class="widget-head">
      <svg width="16" height="18" viewBox="0 0 16 18"><path d="M10 2H2v15h11V9" fill="none" stroke="#fff" stroke-width="1.8"/><path d="M6 12l1-3 7-7 2 2-7 7z" fill="#fff"/></svg>
      QUICK CONTACT
    </div>
  </section>

  <footer class="abs footer">
    <h4 style="left:118px;top:17px;width:105px">Quick Links</h4>
    <ul class="quick">
      <li>Home</li><li>About Us</li><li>Consulting Services</li><li>News &amp; Events</li><li>FAQ's</li><li>Contact Us</li>
    </ul>
    <div class="vrule" style="left:254px"></div>
    <h4 style="left:288px;top:17px;width:376px">Contact Us</h4>
    <div class="map" role="img" aria-label="Street map showing the office location"></div>
    <div class="contact-line" style="top:52px">
      <svg width="17" height="15" viewBox="0 0 17 15"><path d="M8.5 1 1 8h2v6h4v-4h3v4h4V8h2z" fill="#eee"/></svg>
      <span>Lorem ipsum dolor sit amet, conse<br>adipiscing elit, sed diam nonummy.</span>
    </div>
    <div class="contact-line" style="top:88px">
      <svg width="17" height="17" viewBox="0 0 17 17"><circle cx="8.5" cy="8.5" r="7.5" fill="none" stroke="#eee" stroke-width="1.4"/><path d="M6 4c-1 2 0 4 2 6s4 3 5 2l-1-1-2 1c-1-1-2-2-3-4l1-1z" fill="#eee"/></svg>
      <span>123.456.7890</span>
    </div>
    <div class="contact-line" style="top:114px">
      <span style="font-size:16px;width:17px">@</span>
      <span>info@qrvadvisors-example.com</span>
    </div>
    <div class="vrule" style="left:700px"></div>
    <div class="foot-brand">QRV</div>
    <div class="foot-social"><span></span><span></span><span></span></div>
    <p class="copyright">© 2014 qrvadvisors-example. All Rights Reserved .</p>
  </footer>

</div>
</body>
</html>
```